Business card design for holistic health care clinic

We need a double-sided business card design for our holistic health care clinic that integrates our logo design and also its color scheme. My business is called Valmira. It is an integrative medicine clinic. You have already done the logo for me. Please ensure an elegant and upscale design that is not cluttered, but still has all the necessary information (please see below for details).

Target Market(s)

Wellness, fitness, rehabilitation for educated, well-traveled open-minded clients who are focused on natural, organic, balanced and preventive healthcare and lifestyle.

Industry/Entity Type

Medical

Contact Information for Business Card

Modern, clean.

Number of Pages Required

1 page

Font styles to use
Serif
Sans Serif

Colors

Designer to choose colors to be used in the design.

Requirements
Must have
• Logo on one side, all other information on the other side.
• Other information should include:
• Tobias Wrenfeld - DOE, CPT, LMT
• 4100 East Marrow Drive
• Austin, TX 78119
• 512 555 0148
• 818 555 0192
• info@ValmiraHealth.example
• t.wrenfeld@ValmiraHealth.example
Nice to have
• Darker background on front - but not totally black - shaded/dark gray.

```html
<!DOCTYPE html>
<html lang="en">
<head>
<meta charset="utf-8">
<title>Valmira business cards</title>
<link rel="stylesheet" href="https://fonts.googleapis.com/css2?family=Montserrat:wght@700;800&family=Nunito:wght@700&family=Questrial&display=swap">
<style>
  :root {
    --blue: #0a8fd0;
    --blue-soft: #4fb0e0;
    --grey: #a6a6a6;
    --paper: #f1f1f1;
    --ink: #3c3c3c;
    --white: #ffffff;
    --stage: #2b2b2b;
  }
  * { margin: 0; padding: 0; box-sizing: border-box; }
  html, body { width: 1200px; height: 961px; overflow: hidden; }
  body { background: var(--stage); position: relative; font-family: "Questrial", sans-serif; }

  .card { position: absolute; width: 452px; height: 258px; overflow: hidden; }
  .card--grey { background: var(--grey); }
  .card--paper { background: var(--paper); }

  .front-art { position: absolute; inset: 0; }

  .holder { position: absolute; left: 32px; top: 26px; }
  .holder__name { font-family: "Montserrat", sans-serif; font-weight: 800; font-size: 16px; color: var(--blue); letter-spacing: .3px; line-height: 1.1; }
  .holder__creds { font-family: "Montserrat", sans-serif; font-weight: 700; font-size: 8.5px; color: var(--blue); margin-top: 1px; }
  .holder__line { font-size: 11px; line-height: 14px; margin-top: 1px; }
  .card--grey .holder__line { color: var(--white); }
  .card--paper .holder__line { color: var(--ink); }

  .clinic { position: absolute; right: 31px; top: 170px; text-align: right; color: var(--white); font-size: 11.5px; line-height: 13px; }
  .clinic__contact { margin-top: 7px; line-height: 15px; }
  .clinic__contact span { display: inline-flex; align-items: center; gap: 5px; }
  .clinic__contact svg { width: 10px; height: 10px; }

  .brand { position: absolute; left: 0; right: 0; top: 78px; text-align: center; }
  .brand__name { font-family: "Montserrat", sans-serif; font-weight: 800; font-size: 52px; color: var(--blue); letter-spacing: 1px; line-height: 1; }
  .brand__sub { font-family: "Nunito", sans-serif; font-weight: 700; font-size: 15.5px; color: var(--blue); margin-top: 6px; }
  .tagline { position: absolute; left: 0; right: 0; top: 212px; display: flex; justify-content: center; align-items: center; gap: 2px; font-size: 13px; }
  .tagline::before, .tagline::after { content: ""; width: 48px; height: 1px; }
  .card--paper .tagline { color: var(--blue); }
  .card--paper .tagline::before, .card--paper .tagline::after { background: var(--ink); }
  .card--grey .tagline { color: var(--white); }
  .card--grey .tagline::before, .card--grey .tagline::after { background: var(--white); }
</style>
</head>
<body>

<!-- Front, grey -->
<section class="card card--grey" style="left:133px; top:206px;">
  <svg class="front-art" viewBox="0 0 452 258" width="452" height="258">
    <path d="M310 0 C300 70 250 110 230 150 C205 200 150 230 100 258 L452 258 L452 0 Z" fill="var(--blue)"/>
    <path d="M300 10 C310 60 290 100 250 120 C220 140 190 160 170 200 C150 235 120 250 110 258 L150 258 C190 230 220 200 240 175 C270 140 310 100 300 10 Z" fill="var(--blue-soft)" opacity=".55" role="img" aria-label="Winged figure illustration"/>
  </svg>
  <div class="holder">
    <p class="holder__name">TOBIAS WRENFELD</p>
    <p class="holder__creds">DOE, CPT, LMT</p>
    <p class="holder__line">t.wrenfeld@ValmiraHealth.example</p>
    <p class="holder__line">818 555 0192</p>
  </div>
  <div class="clinic">
    <p>4100 East Marrow Drive</p>
    <p>Austin, TX 78119</p>
    <div class="clinic__contact">
      <p><span>512 555 0148 <svg viewBox="0 0 10 10"><path d="M2 0.5 L3.6 2.8 L2.7 3.8 C3.3 5.2 4.8 6.7 6.2 7.3 L7.2 6.4 L9.5 8 L8.4 9.5 C4.5 9.2 0.8 5.5 0.5 1.6 Z" fill="var(--white)"/></svg></span></p>
      <p><span>www.ValmiraHealth.example <svg viewBox="0 0 10 10"><circle cx="5" cy="5" r="4.5" fill="var(--white)"/><path d="M0.5 5 H9.5 M5 0.5 C2.5 3 2.5 7 5 9.5 C7.5 7 7.5 3 5 0.5" stroke="var(--blue)" stroke-width=".7" fill="none"/></svg></span></p>
    </div>
  </div>
</section>

<!-- Front, paper -->
<section class="card card--paper" style="left:617px; top:206px;">
  <svg class="front-art" viewBox="0 0 452 258" width="452" height="258">
    <path d="M310 0 C300 70 250 110 230 150 C205 200 150 230 100 258 L452 258 L452 0 Z" fill="var(--blue)"/>
    <path d="M300 10 C310 60 290 100 250 120 C220 140 190 160 170 200 C150 235 120 250 110 258 L150 258 C190 230 220 200 240 175 C270 140 310 100 300 10 Z" fill="var(--blue-soft)" opacity=".55" role="img" aria-label="Winged figure illustration"/>
  </svg>
  <div class="holder">
    <p class="holder__name">TOBIAS WRENFELD</p>
    <p class="holder__creds">DOE, CPT, LMT</p>
    <p class="holder__line">t.wrenfeld@ValmiraHealth.example</p>
    <p class="holder__line">818 555 0192</p>
  </div>
  <div class="clinic">
    <p>4100 East Marrow Drive</p>
    <p>Austin, TX 78119</p>
    <div class="clinic__contact">
      <p><span>512 555 0148 <svg viewBox="0 0 10 10"><path d="M2 0.5 L3.6 2.8 L2.7 3.8 C3.3 5.2 4.8 6.7 6.2 7.3 L7.2 6.4 L9.5 8 L8.4 9.5 C4.5 9.2 0.8 5.5 0.5 1.6 Z" fill="var(--white)"/></svg></span></p>
      <p><span>www.ValmiraHealth.example <svg viewBox="0 0 10 10"><circle cx="5" cy="5" r="4.5" fill="var(--white)"/><path d="M0.5 5 H9.5 M5 0.5 C2.5 3 2.5 7 5 9.5 C7.5 7 7.5 3 5 0.5" stroke="var(--blue)" stroke-width=".7" fill="none"/></svg></span></p>
    </div>
  </div>
</section>

<!-- Back, paper -->
<section class="card card--paper" style="left:132px; top:496px;">
  <div class="brand">
    <p class="brand__name">VALMIRA</p>
    <p class="brand__sub">Integrative Holistic Medicine</p>
  </div>
  <p class="tagline">Helping the body help itself</p>
</section>

<!-- Back, grey -->
<section class="card card--grey" style="left:615px; top:496px;">
  <div class="brand">
    <p class="brand__name">VALMIRA</p>
    <p class="brand__sub">Integrative Holistic Medicine</p>
  </div>
  <p class="tagline">Helping the body help itself</p>
</section>

</body>
</html>
```